International business needs business cards

Our company, DRV Ventures Inc. is in the business of supplying a range construction products with particular emphasis on CEMENT. We have developed our own brand - TORVAN SUPPLIES - with which to infiltrate the market. We are launching our brand of cement (TORVAN Type IS Cement) into the Caribbean which is unlike anything this market has ever seen. A monopoly has existed here for the past 60-odd years and the market has now opened to allow the importation of other brands and consumers are anxious and ready for change/improvement. We are very excited to be launching and want to make a great first impression. We will be conducting workshops and seminars (from government level to the hardware store owners) and we want our business card to give us the strong, confident introduction that we need.

Target Market(s)

construction; builders; engineers; home owners

Industry/Entity Type

Construction

Contact Information for Business Card

Marisol Depree
CEO
cell # 1 555 4180736
Ground floor,Lindell Plaza Suite 2734
Port Alder,Grand Selva
Selva Islands,KY1-4823
EMAIL: m.depree@drvventuresinc.example
web site drvventuresinc.example

COMPANY: skype info drv.ventures.example

second card
Yvette Brannock-Depree
CFO
CELL# 1 555 607 3941
Port Alder,Grand Selva
Selva Islands,KY1-4823
EMAIL: y.brannockdepree@drvventuresinc.example
website drvventuresinc.example

Requirements
Must have
• Business cards must display BOTH logos - DRV is the company and TORVAN is the brand.

```html
<!DOCTYPE html>
<html lang="en">
<head>
<meta charset="utf-8">
<title>DRV Ventures Inc. – Business Card</title>
<link rel="stylesheet" href="https://fonts.googleapis.com/css2?family=Arimo:wght@400;700&display=swap">
<style>
  :root {
    --brand-red: #8e1a20;
    --brand-red-deep: #6f1318;
    --brand-red-light: #a5262c;
    --ink: #1c1c1c;
    --muted: #555555;
    --paper: #ffffff;
    --stage: #e6e3df;
  }
  * { box-sizing: border-box; margin: 0; padding: 0; }
  html, body { width: 1200px; height: 950px; overflow: hidden; }
  body {
    background: var(--stage);
    font-family: "Arimo", Arial, sans-serif;
    position: relative;
  }
  .card {
    position: absolute;
    left: 250px;
    width: 700px;
    height: 420px;
    overflow: hidden;
    box-shadow: 0 6px 18px rgba(0,0,0,0.18);
  }

  /* Back side */
  .card-back {
    top: 40px;
    background: linear-gradient(135deg, var(--brand-red) 0%, var(--brand-red-deep) 100%);
    color: var(--paper);
  }
  .brand-mark {
    position: absolute;
    top: 160px; left: 0; right: 0;
    display: flex; align-items: center; justify-content: center; gap: 14px;
  }
  .brand-mark .dot {
    width: 26px; height: 26px; border-radius: 50%; background: var(--paper);
  }
  .brand-mark .name {
    font-weight: 700; font-size: 38px; letter-spacing: 4px; color: var(--paper);
  }
  .back-url {
    position: absolute; top: 300px; left: 0; right: 0;
    text-align: center; font-size: 17px; letter-spacing: 2.5px;
  }

  /* Front side */
  .card-front { top: 490px; background: var(--paper); color: var(--ink); }
  .company-mark {
    position: absolute; top: 44px; left: 0; right: 0;
    display: flex; align-items: center; justify-content: center; gap: 14px;
  }
  .company-mark .square { width: 44px; height: 44px; background: var(--brand-red); }
  .company-mark .name { font-weight: 700; font-size: 34px; color: var(--ink); }

  .name-band {
    position: absolute; top: 124px; left: 0; width: 100%; height: 86px;
    background: linear-gradient(90deg, var(--brand-red-deep), var(--brand-red) 60%, var(--brand-red-light));
    color: var(--paper); text-align: center; padding-top: 19px;
  }
  .person-name { font-size: 26px; font-weight: 700; line-height: 30px; }
  .person-title { font-size: 14px; margin-top: 4px; letter-spacing: 1px; }

  .contact-list {
    position: absolute; top: 224px; right: 34px;
    list-style: none; text-align: right; font-size: 16px; color: var(--muted);
  }
  .contact-list li {
    display: flex; align-items: center; justify-content: flex-end; gap: 12px; height: 22px;
  }
  .contact-list svg { width: 16px; height: 16px; fill: var(--brand-red); }

  .accent-stripe {
    position: absolute; top: 294px; left: 0; width: 400px; height: 30px;
    background: linear-gradient(90deg, var(--brand-red-deep), var(--brand-red));
  }
  .address {
    position: absolute; top: 334px; left: 34px;
    font-style: normal; font-size: 15px; line-height: 18px; color: var(--muted);
  }
</style>
</head>
<body>

  <section class="card card-back" aria-label="Card back">
    <div class="brand-mark">
      <span class="dot"></span>
      <span class="name">TORVAN</span>
    </div>
    <p class="back-url">www.drvventuresinc.example</p>
  </section>

  <section class="card card-front" aria-label="Card front">
    <div class="company-mark">
      <span class="square"></span>
      <span class="name">DRV Ventures Inc.</span>
    </div>

    <div class="name-band">
      <p class="person-name">Marisol Depree</p>
      <p class="person-title">CEO</p>
    </div>

    <ul class="contact-list">
      <li>1 555 4180736
        <svg viewBox="0 0 16 16" aria-hidden="true"><path d="M4 1h8a1 1 0 0 1 1 1v12a1 1 0 0 1-1 1H4a1 1 0 0 1-1-1V2a1 1 0 0 1 1-1zm1 2v9h6V3z"/></svg>
      </li>
      <li>m.depree@drvventuresinc.example
        <svg viewBox="0 0 16 16" aria-hidden="true"><path d="M1 3h14v10H1zm1.5 1.2L8 8.5l5.5-4.3z"/></svg>
      </li>
      <li>drvventuresinc.example
        <svg viewBox="0 0 16 16" aria-hidden="true"><circle cx="8" cy="8" r="7"/></svg>
      </li>
    </ul>

    <div class="accent-stripe"></div>

    <address class="address">
      Ground floor<br>
      Lindell Plaza Suite 2734<br>
      Port Alder,Grand Selva<br>
      Selva Islands,KY1-4823
    </address>
  </section>

</body>
</html>
```